Website for Scientific & Engineering Organization

Overview

The objective is to design a professional, easy-to-navigate, and visually appealing website for the <Enclosed Organization (see attached files)>, reflecting their esteemed status in the engineering and scientific community.

Pages:

Home (About Us) : Introduce the organization, highlighting their activities, history, and fellowship. Include a section for latest news highlights.

News and Programme : Dedicated page for news updates and detailed annual programmes

Gallery : This page will feature photographs and descriptions of the society's 'Voyages' and events.

Downloads : A section offering downloadable content such as newsletters and lecture materials, organized for user-friendliness.

Members Section : A private area for members to access exclusive content. Alternatively, a 'Membership' page with joining details and benefits if more public-facing content is preferred.

Design Elements:

Layout : A linear layout with a fixed top navigation bar for easy movement between pages.
Color Scheme : Utilize the provided colors (#395394, #E00053, #0043E1) to create a cohesive and professional aesthetic.
Typography : Use a combination of serif for headings and sans-serif for body text, ensuring readability and elegance.

Features:

Responsive Design : The design will accommodate various devices, ensuring consistency across mobiles, tablets, and desktops.

Accessibility : Design for all users with adequate spacing around elements and color contrasts

Content Strategy (Visual Focus):

Home Page : Visual emphasis on the introduction, mission, and recent 'Voyages' with engaging imagery and concise text.
News and Programme : Clear, visually distinct sections for news and the annual schedule
Gallery : A visually rich page with a grid or album layout, allowing users to easily browse through the years and events.
Downloads : Neatly organized sections with clear labels and icons to represent the different types of available downloads. Downloads are PDF newsletter/flyers/programmes etc...
Members Section/Membership : A design that conveys exclusivity and value, encouraging sign-ups and engagement from members.
Design Considerations:

Consistency : Ensure the design reflects the organization's heritage and professionalism throughout all pages.
User Experience : Focus on intuitive navigation and information architecture to guide visitors smoothly through the site.
Visual Hierarchy : Use size, color, and layout to emphasize key areas and direct user attention effectively.
Final Notes:

This design spec focuses on creating a web presence that mirrors the organization's prestige and heritage, providing an engaging, informative platform for members and the public alike. The design will be crafted to allow for easy content updates and adaptability, ensuring a long-lasting and effective website.

Target Market(s)

Non profit science and engineering. Older people

Industry/Entity Type

Non profit scientific organization

Number of Pages Required

5+ page

Requirements
Should not have
• No search feature

```html
<!DOCTYPE html>
<html lang="en">
<head>
<meta charset="utf-8">
<title>ASTRA British Section</title>
<link rel="stylesheet" href="https://fonts.googleapis.com/css2?family=Playfair+Display:wght@600;700;800&family=Poppins:wght@400;500;600&display=swap">
<style>
:root{
  --navy:#395394;
  --navy-dark:#1f2f63;
  --crimson:#E00053;
  --royal:#0043E1;
  --ink:#1b1f2e;
  --muted:#5b6072;
  --grey-bg:#eeeff3;
  --pink:#e2336b;
  --footer:#15171f;
  --white:#ffffff;
}
*{box-sizing:border-box;margin:0;padding:0}
html,body{width:1200px;height:4348px;overflow:hidden}
body{font-family:"Poppins",sans-serif;color:var(--ink);background:var(--white);position:relative}
h1,h2,h3{font-family:"Playfair Display",serif}
a{text-decoration:none;color:inherit}
section,header,footer{position:relative;width:1200px;overflow:hidden}
.btn{display:inline-flex;align-items:center;gap:8px;background:var(--crimson);color:#fff;font-size:13px;font-weight:600;text-transform:uppercase;padding:12px 22px;border-radius:4px;letter-spacing:.3px}
.btn-white{background:#fff;color:var(--ink)}
.btn .arr{width:16px;height:16px;border-radius:50%;background:#fff;color:var(--crimson);display:inline-flex;align-items:center;justify-content:center;font-size:10px}
.btn-white .arr{background:var(--crimson);color:#fff}
.photo{position:absolute;border-radius:4px}

/* header */
.site-header{position:absolute;top:0;left:0;height:70px;z-index:5;background:rgba(255,255,255,.96);box-shadow:0 2px 8px rgba(0,0,0,.06)}
.brand{position:absolute;left:110px;top:10px;display:flex;align-items:center;gap:10px;font-weight:600;font-size:26px;color:var(--navy)}
.brand-dot{width:40px;height:40px;border-radius:50%;background:var(--crimson)}
.brand small{display:block;font-size:9px;color:var(--muted);font-weight:500;letter-spacing:.5px}
.top-contacts{position:absolute;right:110px;top:4px;display:flex;gap:26px;align-items:center;font-size:12px}
.top-contacts .ci{display:flex;gap:8px;align-items:center}
.top-contacts .ic{width:26px;height:26px;border-radius:50%;background:var(--navy);display:flex;align-items:center;justify-content:center}
.top-contacts span small{display:block;font-size:9px;color:var(--muted)}
.top-contacts b{font-weight:600;color:var(--ink)}
.signin{background:var(--crimson);color:#fff;font-weight:600;font-size:11px;padding:6px 16px;border-radius:3px}
.main-nav{position:absolute;right:110px;top:42px;display:flex;background:var(--navy);border-radius:3px 3px 0 0}
.main-nav a{color:#fff;font-size:12px;padding:6px 16px;font-weight:500}

/* hero */
.hero{height:880px;background:linear-gradient(90deg,#fafbfd 0%,#f3f4f8 45%,#d4dae6 100%)}
.hero-image{position:absolute;right:0;top:0;width:760px;height:840px;background:radial-gradient(ellipse at 40% 45%,#f2efe9 0%,#b4bfd1 45%,#74839f 100%);-webkit-mask-image:linear-gradient(90deg,transparent 0%,#000 35%);mask-image:linear-gradient(90deg,transparent 0%,#000 35%)}
.hero-copy{position:absolute;left:140px;top:360px;width:680px}
.hero-copy h1{font-size:30px;line-height:1.6;font-weight:800;color:var(--ink);text-transform:uppercase}
.hero-copy .hl-red{color:var(--crimson)}
.hero-copy .hl-blue{color:var(--navy)}
.hero-copy .btn{margin-top:26px}
.hero-edge{position:absolute;left:0;bottom:0}

/* features */
.features{height:200px;display:flex;justify-content:center;gap:70px;padding-top:10px}
.feature{width:280px;text-align:center}
.feature-icon{width:90px;height:80px;margin:0 auto 10px;position:relative}
.feature-icon .num{position:absolute;left:20px;top:-2px;font-family:"Playfair Display",serif;font-size:72px;font-weight:700;color:#fff;-webkit-text-stroke:2px var(--navy);line-height:1}
.feature-icon .badge{position:absolute;right:4px;bottom:8px;width:30px;height:30px;border-radius:50%;background:var(--crimson)}
.feature p{font-size:13px;color:var(--muted);line-height:1.55}
.feature .btn{margin-top:14px;padding:9px 18px;font-size:11px}

/* activities */
.activities{height:520px}
.activities-panel{position:absolute;left:0;top:0;width:540px;height:520px;background:var(--grey-bg)}
.tab-list{position:absolute;left:140px;top:70px;width:380px;list-style:none}
.tab{display:flex;align-items:center;gap:20px;height:82px;margin-bottom:22px;border-radius:41px;background:#fff;border:1px solid #dde0e8;padding-left:8px;font-size:15px;font-weight:500;color:var(--ink)}
.tab .tab-ic{width:66px;height:66px;border-radius:50%;background:var(--navy);display:flex;align-items:center;justify-content:center}
.tab.active{background:var(--crimson);color:#fff;border-color:var(--crimson);margin-right:-30px}
.tab.active .tab-ic{background:#fff}
.activities-copy{position:absolute;left:620px;top:70px;width:440px}
.section-title{font-size:38px;font-weight:700;color:var(--ink);text-transform:uppercase}
.section-title .accent{color:var(--navy)}
.activities-copy p{font-size:13px;color:var(--muted);line-height:1.65;margin-top:16px}
.activities-copy .btn{margin-top:22px}

/* news */
.news{height:730px;background:linear-gradient(180deg,var(--navy) 0%,var(--navy-dark) 100%)}
.news-edge{position:absolute;top:0;left:0}
.news .section-title{position:absolute;top:130px;width:100%;text-align:center;color:#fff}
.news .section-title .accent{color:var(--crimson)}
.cards{position:absolute;top:210px;left:120px;display:flex;gap:30px}
.card{width:300px;background:#fff;border-radius:4px;overflow:hidden}
.card-img{height:200px;position:relative}
.date-badge{position:absolute;left:14px;bottom:-14px;background:var(--crimson);color:#fff;font-size:11px;font-weight:500;padding:6px 12px;border-radius:3px;display:flex;align-items:center;gap:6px}
.card-body{padding:30px 18px 22px;height:230px}
.card-body h3{font-family:"Poppins",sans-serif;font-size:15px;font-weight:600;line-height:1.4;color:var(--ink)}
.card-body p{font-size:12px;color:var(--muted);line-height:1.6;margin-top:10px;text-align:justify}
.read-more{display:inline-flex;gap:6px;align-items:center;margin-top:12px;font-size:12px;font-weight:600;color:var(--navy)}
.dots{position:absolute;left:0;width:100%;display:flex;justify-content:center;gap:8px}
.dots i{width:9px;height:9px;border-radius:50%;background:#aeb4c8;display:block}
.dots i.on{background:var(--crimson)}
.news .dots{top:680px}
.news .dots i{background:rgba(255,255,255,.45)}
.news .dots i.on{background:#fff}

/* gallery */
.gallery{height:840px}
.gallery .section-title{position:absolute;top:60px;width:100%;text-align:center}
.gallery .section-title .accent{color:var(--crimson)}
.gallery .dots{top:790px}

/* newsletter */
.newsletter{height:400px;background:linear-gradient(135deg,#e54779 0%,var(--pink) 50%,#cf1f5c 100%);text-align:center;color:#fff}
.newsletter .section-title{padding-top:60px;color:#fff}
.newsletter .section-title .accent{color:var(--navy-dark)}
.subscribe-form{margin:30px auto 0;display:flex;justify-content:center}
.subscribe-form .field{width:300px;height:40px;background:#fff;border-radius:3px 0 0 3px;font-size:12px;color:#9a9ead;display:flex;align-items:center;padding-left:16px}
.subscribe-form .go{height:40px;background:var(--navy);color:#fff;font-size:12px;font-weight:600;padding:0 20px;display:flex;align-items:center;border-radius:0 3px 3px 0}
.newsletter p{width:720px;margin:30px auto 0;font-size:15px;line-height:1.6}
.newsletter .btn{margin-top:26px}

/* members */
.members{height:520px}
.members-copy{position:absolute;left:140px;top:90px;width:430px}
.members-copy p{font-size:13px;color:var(--muted);line-height:1.65;margin-top:16px}
.members-copy .btn{margin-top:24px}
.members-image{position:absolute;left:660px;top:40px;width:420px;height:440px;background:radial-gradient(ellipse at 60% 50%,#e3a24a 0%,#8a6b52 45%,#3e4556 100%);-webkit-mask-image:linear-gradient(90deg,transparent 0%,#000 30%);mask-image:linear-gradient(90deg,transparent 0%,#000 30%)}

/* footer */
.site-footer{height:258px;background:var(--footer);color:#fff}
.footer-edge{position:absolute;top:0;left:0}
.footer-brand{position:absolute;top:56px;left:0;width:100%;display:flex;justify-content:center}
.footer-brand .box{background:#fff;border-radius:4px;padding:10px 18px;display:flex;align-items:center;gap:10px;font-size:26px;font-weight:600;color:var(--navy)}
.footer-brand .brand-dot{width:36px;height:36px}
.footer-contacts{position:absolute;top:142px;width:100%;display:flex;justify-content:center;gap:30px;font-size:12px}
.footer-contacts span{display:flex;align-items:center;gap:8px}
.footer-contacts i{width:6px;height:6px;border-radius:50%;background:var(--crimson);display:block}
.footer-nav{position:absolute;top:184px;width:100%;display:flex;justify-content:center;font-size:12px;font-weight:600}
.footer-nav a{padding:0 22px;border-right:1px solid rgba(255,255,255,.4)}
.footer-nav a:last-child{border-right:0}
.copyright{position:absolute;bottom:0;width:100%;text-align:center;font-size:11px;color:#b8bbc6;border-top:1px solid #2d303b;padding:10px 0}
</style>
</head>
<body>

<header class="site-header">
  <div class="brand"><span class="brand-dot"></span><span>ASTRA<small>BRITISH SECTION</small></span></div>
  <div class="top-contacts">
    <div class="ci"><span class="ic"><svg width="12" height="12" viewBox="0 0 24 24"><path d="M2 5h20v14H2z M2 5l10 8 10-8" fill="none" stroke="#fff" stroke-width="2"/></svg></span><span><small>Email</small><b>info@astra-society.org</b></span></div>
    <div class="ci"><span class="ic"><svg width="12" height="12" viewBox="0 0 24 24"><path d="M6 2l4 5-2 3c1.5 3 3 4.5 6 6l3-2 5 4-3 4C9 21 3 15 2 5z" fill="#fff"/></svg></span><span><small>Call us</small><b>+1 555 014 2290</b></span></div>
    <a class="signin" href="#">SIGN IN</a>
  </div>
  <nav class="main-nav">
    <a href="#">About Us ⌄</a><a href="#">News &amp; Programme ⌄</a><a href="#">Gallery</a><a href="#">Downloads ⌄</a><a href="#">Contact ⌄</a><a href="#">Members Section ⌄</a>
  </nav>
</header>

<section class="hero">
  <div class="hero-image" role="img" aria-label="Engineer in hard hat looking over a city skyline"></div>
  <div class="hero-copy">
    <h1>Welcome to the <span class="hl-red">British Section</span><br>of the <span class="hl-blue">ASTRA sharing knowledge</span><br>and a love of France</h1>
    <a class="btn" href="#">Get Started <span class="arr">›</span></a>
  </div>
  <svg class="hero-edge" width="1200" height="110" viewBox="0 0 1200 110">
    <polygon points="0,0 600,70 1200,0 1200,110 0,110" fill="#fff"/>
    <polyline points="0,12 600,84 1200,12" fill="none" stroke="#395394" stroke-width="8"/>
    <polyline points="0,26 600,98 1200,26" fill="none" stroke="#E00053" stroke-width="6"/>
  </svg>
</section>

<section class="features">
  <div class="feature">
    <div class="feature-icon"><span class="num">1</span><span class="badge"></span></div>
    <p>An informal society of engineers and scientists, giving equal importance to the quality of our technical activities and our fellowship.</p>
  </div>
  <div class="feature">
    <div class="feature-icon"><span class="num">2</span><span class="badge"></span></div>
    <p>We provide high quality lectures and technical visits on diverse engineering and scientific subjects, and the enjoyment of French culture and cuisine.</p>
  </div>
  <div class="feature">
    <div class="feature-icon"><span class="num">3</span><span class="badge"></span></div>
    <p>New members are always welcome</p>
    <a class="btn" href="#">Learn More <span class="arr">›</span></a>
  </div>
</section>

<section class="activities">
  <div class="activities-panel"></div>
  <ul class="tab-list">
    <li class="tab"><span class="tab-ic"><svg width="24" height="24" viewBox="0 0 24 24"><circle cx="12" cy="8" r="4" fill="#fff"/><path d="M4 21c0-5 4-7 8-7s8 2 8 7z" fill="#fff"/></svg></span>Introduce The Organization</li>
    <li class="tab active"><span class="tab-ic"><svg width="24" height="24" viewBox="0 0 24 24"><path d="M4 20h16M7 20V10M12 20V5M17 20v-7" stroke="#E00053" stroke-width="2.5"/></svg></span>Highlighting Their Activities</li>
    <li class="tab"><span class="tab-ic"><svg width="24" height="24" viewBox="0 0 24 24"><circle cx="12" cy="12" r="8" fill="none" stroke="#fff" stroke-width="2"/><path d="M12 7v5l3 3" stroke="#fff" stroke-width="2" fill="none"/></svg></span>History</li>
    <li class="tab"><span class="tab-ic"><svg width="24" height="24" viewBox="0 0 24 24"><circle cx="8" cy="9" r="3" fill="#fff"/><circle cx="16" cy="9" r="3" fill="#fff"/><path d="M2 20c0-4 3-6 6-6s6 2 6 6zM10 20c0-4 3-6 6-6s6 2 6 6z" fill="#fff"/></svg></span>Fellowship</li>
  </ul>
  <div class="activities-copy">
    <h2 class="section-title">Our <span class="accent">Activities</span></h2>
    <p>Five or six high quality technical lectures are arranged throughout the year at a number of London venues followed by dinner. Memorable lectures have included topics as diverse as the building of great domes, supersonic flight, the origins of SI standard measurements and the current Antarctic research programme.</p>
    <p>There are normally two 'Voyages' each year of three or four days each, generally but not exclusively in France, where visits to technical or cultural establishments and major construction sites are included. The 'Voyages' have equally important and enjoyable technical and social components, and of course provide the opportunity and time to relax, enjoy and sample French culture and cuisine.</p>
    <a class="btn" href="#">Learn More <span class="arr">›</span></a>
  </div>
</section>

<section class="news">
  <svg class="news-edge" width="1200" height="90" viewBox="0 0 1200 90">
    <polygon points="0,0 1200,0 1200,10 600,80 0,10" fill="#fff"/>
    <polyline points="0,14 600,84 1200,14" fill="none" stroke="#E00053" stroke-width="5"/>
  </svg>
  <h2 class="section-title">News and <span class="accent">Programmes</span></h2>
  <div class="cards">
    <article class="card">
      <div class="card-img" role="img" aria-label="Fire investigators examining a burnt building" style="background:linear-gradient(160deg,#6d6a63,#2e2c2a)"><span class="date-badge">▣ Mon 21, Jan 2024</span></div>
      <div class="card-body">
        <h3>Incoming President's Inaugural lecture and dinner</h3>
        <p>Forensic Fire Investigation: The Underpinning Fire Science And Investigative Methodology.</p>
        <a class="read-more" href="#">READ MORE ›</a>
      </div>
    </article>
    <article class="card">
      <div class="card-img" role="img" aria-label="Wildfire burning near homes at night" style="background:linear-gradient(160deg,#f08a2c,#8a2a12 60%,#2a120c)"><span class="date-badge">▣ Tue 13, Feb 2024</span></div>
      <div class="card-body">
        <h3>Evening Lecture and Dinner</h3>
        <p>How To Protect People And Homes From Wildfires: Planning, Engineering And Computer Models.</p>
        <a class="read-more" href="#">READ MORE ›</a>
      </div>
    </article>
    <article class="card">
      <div class="card-img" role="img" aria-label="Tower block on fire against a blue sky" style="background:linear-gradient(160deg,#8fb6de,#55677e 55%,#c0552a)"><span class="date-badge">▣ Tue 05, Mar 2024</span></div>
      <div class="card-body">
        <h3>Evening Lecture and Dinner</h3>
        <p>Unplanned Adventures In Fire Science, Engineering, And Regulation: Case Study at the Riverside Hall.</p>
        <a class="read-more" href="#">READ MORE ›</a>
      </div>
    </article>
  </div>
  <div class="dots"><i></i><i class="on"></i><i></i></div>
</section>

<section class="gallery">
  <h2 class="section-title">Our <span class="accent">Gallery</span></h2>
  <div class="photo" role="img" aria-label="Formal dinner hall with chandeliers" style="left:140px;top:160px;width:220px;height:270px;background:linear-gradient(160deg,#c99a5a,#6b3d22)"></div>
  <div class="photo" role="img" aria-label="Engineers in hard hats on a site" style="left:140px;top:440px;width:220px;height:300px;background:linear-gradient(160deg,#e7d16a,#6f7a4e)"></div>
  <div class="photo" role="img" aria-label="Scientists working in a laboratory" style="left:372px;top:160px;width:220px;height:370px;background:linear-gradient(160deg,#e9eef3,#8aa3bd)"></div>
  <div class="photo" role="img" aria-label="Plant seedlings under research" style="left:372px;top:540px;width:220px;height:200px;background:linear-gradient(160deg,#9cc46a,#2f5a2a)"></div>
  <div class="photo" role="img" aria-label="Group of members on a cultural visit" style="left:604px;top:160px;width:220px;height:190px;background:linear-gradient(160deg,#b9c7d6,#6f7d8c)"></div>
  <div class="photo" role="img" aria-label="Members gathered at an event" style="left:604px;top:360px;width:220px;height:380px;background:linear-gradient(160deg,#7f8fa3,#2f3a4b)"></div>
  <div class="photo" role="img" aria-label="Guests at a reception in a hall" style="left:836px;top:160px;width:224px;height:220px;background:linear-gradient(160deg,#d9b57c,#7a5432)"></div>
  <div class="photo" role="img" aria-label="Historic building exterior" style="left:836px;top:390px;width:224px;height:350px;background:linear-gradient(160deg,#c7ccd3,#5d6572)"></div>
  <div class="dots"><i class="on"></i><i></i><i></i><i></i></div>
</section>

<section class="newsletter">
  <h2 class="section-title"><span class="accent">Subscribe</span> to our Newsletter</h2>
  <div class="subscribe-form"><span class="field">Enter email here</span><span class="go">SUBSCRIBE</span></div>
  <p>The Society for Engineers and Scientists where they sample French cuisine and culture with their partners as well as continue their professional interests.</p>
  <a class="btn btn-white" href="#">Download Now <span class="arr">›</span></a>
</section>

<section class="members">
  <div class="members-copy">
    <h2 class="section-title">Our <span class="accent">Members</span></h2>
    <p>The origins of the Section lie in civil engineering. For many years, however, in line with the wider parent society in France, we have been open to membership from like-minded people from all fields of engineering and science.</p>
    <p>We are always delighted to welcome new members. If you would like to join us or would like further information on membership, please visit Membership, contact an existing member, or the Membership Secretary, secretary@astra-society.org</p>
    <a class="btn" href="#">Learn More <span class="arr">›</span></a>
  </div>
  <div class="members-image" role="img" aria-label="Engineers in hard hats and safety vests on site"></div>
</section>

<footer class="site-footer">
  <svg class="footer-edge" width="1200" height="40" viewBox="0 0 1200 40">
    <polygon points="0,0 1200,0 1200,4 600,30 0,4" fill="#fff"/>
    <polyline points="0,8 600,34 1200,8" fill="none" stroke="#395394" stroke-width="5"/>
    <polyline points="0,2 600,28 1200,2" fill="none" stroke="#E00053" stroke-width="3"/>
  </svg>
  <div class="footer-brand"><div class="box"><span class="brand-dot"></span>ASTRA</div></div>
  <div class="footer-contacts">
    <span><i></i>+1 555 014 2290</span>
    <span><i></i>123, Lorem ipsum dolor sit amet, consectetur adipiscing elit.</span>
    <span><i></i>info@astra-society.org</span>
  </div>
  <nav class="footer-nav"><a href="#">ABOUT US</a><a href="#">NEWS &amp; PROGRAMME</a><a href="#">GALLERY</a><a href="#">DOWNLOADS</a><a href="#">CONTACT US</a><a href="#">MEMBERS SECTION</a></nav>
  <div class="copyright">Copyright 2024 ASTRA | All Rights Reserved</div>
</footer>

</body>
</html>
```